Accountant services flyer & marketing portfolio

I require a design for a marketing portfolio of blank templates for a flyer, product brochure, report cover for A4 based on our style - current logo, letterhead, website look and feel - that can be updated in publisher or word with relevant marketing and company information editorial material and text. It will be either printed A4 or saved as PDF and distributed

Target Market(s)

small business and investment / superfund clients

Industry/Entity Type

Accountant

Font styles to use
Sans Serif

Requirements
Must have
• Instyle of letterhead and website
Professional body logos
Space to input text
Relevant happy images
Nice to have
• Images of happy lifestyle types retirees, young families and mid-aged
tradesmen and professionals

```html
<!DOCTYPE html>
<html lang="en">
<head>
<meta charset="utf-8">
<title>Solstice Advisory – Brochure</title>
<link rel="stylesheet" href="https://fonts.googleapis.com/css2?family=Montserrat:wght@400;600;700;800&family=Open+Sans:wght@400;600&display=swap">
<style>
:root{
  --bg:#e4e4e4;
  --paper:#f7f7f7;
  --orange:#e8582a;
  --orange-mid:#ee7a32;
  --yellow:#f0b23c;
  --ink:#2b2b2b;
  --grey:#6f6f6f;
  --soft:#e4e0e4;
  --line:#f1c9a8;
}
*{box-sizing:border-box;margin:0;padding:0}
html,body{width:1200px;height:2609px;overflow:hidden}
body{background:var(--bg);font-family:"Open Sans",Arial,sans-serif;color:var(--ink);position:relative}
.cover{position:absolute;width:420px;height:594px;background:var(--paper);overflow:hidden;box-shadow:0 14px 30px rgba(0,0,0,.18)}
.cover-bands{position:absolute;inset:0}
.cover-photo{position:absolute;left:42px;top:62px;width:300px;height:340px;background:linear-gradient(150deg,#8a6a4c 0%,#5b4230 45%,#3f2d22 100%)}
.brand{position:absolute;font-family:"Montserrat",sans-serif;font-weight:700;color:var(--orange);letter-spacing:.5px;line-height:1.1}
.brand small{display:block;font-weight:600;font-size:.62em;color:var(--orange);letter-spacing:0}
.cover .brand{top:22px;right:34px;font-size:15px;text-align:right}
.cover-title{position:absolute;left:30px;top:420px;font-family:"Montserrat",sans-serif;font-weight:800;line-height:1}
.cover-title .t1{color:var(--orange);font-size:30px}
.cover-title .t2{color:var(--ink);font-size:35px}
.cover-title .t3{color:var(--ink);font-size:10.5px;margin-top:6px;letter-spacing:.4px}
.cover-title .url{font-family:"Open Sans",sans-serif;font-weight:400;font-size:10px;color:var(--grey);margin-top:12px}
.back-contact{position:absolute;left:36px;top:420px;font-size:10px;color:var(--grey);line-height:1.6}
.back-contact .brand{position:static;font-size:16px;margin-bottom:12px}
.back-contact .row{display:flex;align-items:flex-start;gap:6px}
.back-contact svg{flex:none;margin-top:3px}
.spread{position:absolute;left:150px;top:1830px;width:880px;height:630px;display:flex;box-shadow:0 16px 34px rgba(0,0,0,.2)}
.page{position:relative;width:440px;height:630px;background:var(--paper);overflow:hidden}
.page-header{position:absolute;left:0;top:0;width:440px;height:80px;background:linear-gradient(90deg,#2a1c12 0%,#5a3a1c 50%,#3a2a1e 100%)}
.page-heading{position:absolute;left:44px;top:36px;font-family:"Montserrat",sans-serif;font-weight:700;font-size:20px;color:#fff;letter-spacing:.5px}
.intro{position:absolute;left:44px;top:100px;width:350px;font-size:9.5px;line-height:1.3;color:#444}
.features{position:absolute;left:44px;top:180px;display:grid;grid-template-columns:repeat(3,108px);column-gap:14px;row-gap:20px}
.feature-img{width:88px;height:88px;border-radius:50%;border:4px solid var(--orange);background:linear-gradient(160deg,#c9b9a8,#6d5a4a)}
.feature h3{font-family:"Montserrat",sans-serif;font-weight:700;font-size:11px;color:var(--orange);margin-top:12px;line-height:1.1}
.feature p{font-size:5px;line-height:1.35;color:var(--grey);margin-top:3px;width:96px}
.page-footer{position:absolute;left:42px;right:42px;top:572px;height:24px;display:flex;align-items:flex-end;gap:8px}
.page-footer .brand{position:static;font-size:9px}
.page-footer .rule{flex:1;border-bottom:1px solid #c8c8c8;margin-bottom:4px}
.page-footer .url{background:var(--orange);color:#fff;font-size:8px;padding:1px 6px;border-radius:2px;margin-bottom:1px}
.page-footer .num{width:10px;height:10px;border-radius:50%;border:1px solid var(--orange);font-size:5px;text-align:center;line-height:8px;margin-bottom:1px}
.services-photo{position:absolute;left:228px;top:2px;width:214px;height:214px;border-radius:50%;border:6px solid var(--orange);background:radial-gradient(circle at 50% 40%,#c99a4a 0%,#6b4a22 45%,#1c2233 100%)}
.services-intro{position:absolute;left:42px;top:96px;width:178px;font-size:9.5px;line-height:1.3;color:#444}
.service{position:absolute;width:170px;height:42px;border:1px solid var(--line);background:#fff;display:flex;align-items:center;gap:8px;padding:0 8px}
.service svg{flex:none}
.service h4{font-family:"Montserrat",sans-serif;font-size:5.5px;font-weight:600;color:#333}
.service p{font-size:4.2px;color:#999;line-height:1.3;margin-top:2px}
.trending{position:absolute;left:0;top:350px;width:440px;height:280px;background:var(--soft)}
.trending h2{position:absolute;left:42px;top:22px;font-family:"Montserrat",sans-serif;font-weight:700;font-size:19px;color:var(--orange)}
.trend{position:absolute;top:90px;width:84px;height:90px;background:var(--yellow);color:#fff;font-family:"Montserrat",sans-serif;font-size:7px;font-weight:600;padding:42px 8px 0;text-align:left;line-height:1.3}
.trend-icon{position:absolute;top:-36px;left:6px;width:72px;height:72px;border-radius:50%;background:var(--orange);border:3px solid #fff;box-shadow:0 0 0 2px var(--orange);display:flex;align-items:center;justify-content:center}
</style>
</head>
<body>

<!-- Front cover -->
<section class="cover" style="left:390px;top:90px">
  <svg class="cover-bands" width="420" height="594" aria-hidden="true">
    <defs><linearGradient id="bandA" x1="0" y1="0" x2="0" y2="1"><stop offset="0" stop-color="#e8582a"/><stop offset="1" stop-color="#f0b23c"/></linearGradient></defs>
    <polygon points="344,150 420,118 420,594 330,594" fill="url(#bandA)"/>
    <polygon points="420,430 420,594 200,594" fill="#f0b23c"/>
  </svg>
  <div class="cover-photo" role="img" aria-label="Team of hands joined in a fist bump over a desk with tablet, calculator and papers"></div>
  <div class="brand">SOLSTICE ADVISORY<small>Clear advice. Real results</small></div>
  <div class="cover-title">
    <div class="t1">THE DIGITAL</div>
    <div class="t2">REVOLUTION</div>
    <div class="t3">HAS BEGUNPLAN FOR THE OPPORTUNITY!</div>
    <div class="url">www.solsticeadvisory.com.au</div>
  </div>
</section>

<!-- Back cover -->
<section class="cover" style="left:180px;top:900px">
  <div class="back-contact">
    <div class="brand">SOLSTICE ADVISORY<small>Clear advice. Real results</small></div>
    <div class="row">
      <svg width="9" height="9" viewBox="0 0 24 24"><path fill="#e8582a" d="M6.6 10.8a15 15 0 0 0 6.6 6.6l2.2-2.2a1 1 0 0 1 1-.3 11 11 0 0 0 3.6.6 1 1 0 0 1 1 1V20a1 1 0 0 1-1 1A17 17 0 0 1 3 4a1 1 0 0 1 1-1h3.5a1 1 0 0 1 1 1c0 1.3.2 2.5.6 3.6a1 1 0 0 1-.3 1z"/></svg>
      <div>1300 555 214 &nbsp; 612 4555 0198<br>hello@solsticeadvisory.com<br>www.solsticeadvisory.com.au</div>
    </div>
    <div class="row" style="margin-top:8px">
      <svg width="9" height="9" viewBox="0 0 24 24"><path fill="#e8582a" d="M12 2a7 7 0 0 0-7 7c0 5 7 13 7 13s7-8 7-13a7 7 0 0 0-7-7zm0 9.5A2.5 2.5 0 1 1 12 6.5a2.5 2.5 0 0 1 0 5z"/></svg>
      <div>Suite 4, Level 2, 220 Harbour Road,<br>Gosford NSW 2250</div>
    </div>
  </div>
</section>

<!-- Front cover in open spread -->
<section class="cover" style="left:600px;top:900px">
  <svg class="cover-bands" width="420" height="594" aria-hidden="true">
    <defs><linearGradient id="bandB" x1="0" y1="0" x2="0" y2="1"><stop offset="0" stop-color="#e8582a"/><stop offset="1" stop-color="#f0b23c"/></linearGradient></defs>
    <polygon points="344,150 420,118 420,594 330,594" fill="url(#bandB)"/>
    <polygon points="420,430 420,594 200,594" fill="#f0b23c"/>
  </svg>
  <div class="cover-photo" role="img" aria-label="Team of hands joined in a fist bump over a desk with tablet, calculator and papers"></div>
  <div class="brand">SOLSTICE ADVISORY<small>Clear advice. Real results</small></div>
  <div class="cover-title">
    <div class="t1">THE DIGITAL</div>
    <div class="t2">REVOLUTION</div>
    <div class="t3">HAS BEGUNPLAN FOR THE OPPORTUNITY!</div>
    <div class="url">www.solsticeadvisory.com.au</div>
  </div>
</section>

<!-- Inside spread -->
<section class="spread">
  <article class="page">
    <div class="page-header" role="img" aria-label="City skyline at night"></div>
    <h1 class="page-heading">ABOUT SOLSTICE</h1>
    <p class="intro">For over 35 years Solstice Advisory CEO Martin Hale has prospered on the “Cutting Edge” of Business and Finance. With extensive qualifications, comprehensive and wide ranging hands-on experience, he offers a unique and potent combination of expertise and knowledge that will guarantee superior strategic advice that can really make a difference.</p>
    <div class="features">
      <div class="feature"><div class="feature-img" role="img" aria-label="Hand wearing a smartwatch"></div><h3>WELCOME TO CLIENTS</h3><p>On launch day we opened our doors to offer accounting, wealth and business advice.</p></div>
      <div class="feature"><div class="feature-img" role="img" aria-label="Phone and keyboard on a desk" style="background:linear-gradient(160deg,#9aa0a8,#e88a3a)"></div><h3>OUR VISION</h3><p>The digital revolution has changed how we work and will shape the next decade.</p></div>
      <div class="feature"><div class="feature-img" role="img" aria-label="Team joining hands over a desk"></div><h3>WELCOME ABOARD!</h3><p>Being proactive is our point of difference, with a full suite of accounting services.</p></div>
      <div class="feature"><div class="feature-img" role="img" aria-label="Historic city gate landmark" style="background:linear-gradient(160deg,#8ea2c0,#7a6850)"></div><h3>HISTORY &amp; ACHIEVEMENTS</h3><p>Our firm has a rich vein of qualifications, expertise and experience.</p></div>
      <div class="feature"><div class="feature-img" role="img" aria-label="Portrait of the firm's chief executive" style="background:linear-gradient(160deg,#5f8a4a,#2c3550)"></div><h3>CEO MARTIN HALE</h3><p>I enjoy working closely with clients to help them reach their goals.</p></div>
      <div class="feature"><div class="feature-img" role="img" aria-label="Hands working on papers and a laptop" style="background:linear-gradient(160deg,#d8d2cc,#5c6470)"></div><h3>OURSOURCE CFO SERVICES</h3><p>Business is demanding and owners often get caught in daily detail.</p></div>
    </div>
    <footer class="page-footer"><div class="brand">SOLSTICE ADVISORY<small>Clear advice. Real results</small></div><div class="rule"></div><div class="url">www.solsticeadvisory.com.au</div><div class="num">01</div></footer>
  </article>

  <article class="page">
    <div class="page-header" role="img" aria-label="City skyline at night"></div>
    <div class="services-photo" role="img" aria-label="City towers lit at night reflected on water"></div>
    <h1 class="page-heading" style="left:42px">OUR SERVICES</h1>
    <p class="services-intro">Solstice Advisory is uniquely positioned to offer an unparalleled range of financial advice that incorporates both Business and Personal financial growth strategies.</p>

    <div class="service" style="left:42px;top:180px">
      <svg width="22" height="16" viewBox="0 0 22 16"><path d="M8 2 2 8l6 6M14 2l6 6-6 6" fill="none" stroke="#e8582a" stroke-width="2"/></svg>
      <div><h4>Tax &amp; Accounting</h4><p>Extensive taxation experience and a network of expert consultants.</p></div>
    </div>
    <div class="service" style="left:42px;top:232px">
      <svg width="22" height="18" viewBox="0 0 22 18"><path d="M11 1v15M4 16h14M3 4h16M3 4l-2 6h4zM19 4l-2 6h4z" fill="none" stroke="#e8582a" stroke-width="1.5"/></svg>
      <div><h4>Litigation, Audit &amp; Assurance</h4><p>Areas of expertise include expert witness business valuations.</p></div>
    </div>
    <div class="service" style="left:222px;top:232px">
      <svg width="22" height="20" viewBox="0 0 22 20"><rect x="4" y="3" width="14" height="14" fill="none" stroke="#e8582a" stroke-width="1.5"/><path d="M1 1h4v4H1zM17 1h4v4h-4zM1 15h4v4H1zM17 15h4v4h-4z" fill="none" stroke="#e8582a" stroke-width="1.2"/></svg>
      <div><h4>Superannuation &amp; Financial Planning</h4><p>Helping clients grow, diversify and protect family wealth.</p></div>
    </div>
    <div class="service" style="left:42px;top:284px">
      <svg width="22" height="18" viewBox="0 0 22 18"><path d="M2 17v-3M7 17v-6M12 17v-9M17 17V3" stroke="#e8582a" stroke-width="3"/></svg>
      <div><h4>News</h4></div>
    </div>
    <div class="service" style="left:222px;top:284px">
      <svg width="22" height="18" viewBox="0 0 22 18"><path d="M1 3l5 13 5-11 5 11 5-13" fill="none" stroke="#e8582a" stroke-width="1.5"/></svg>
      <div><h4>Business Improvement Strategies</h4><p>A partner in business coaching and development.</p></div>
    </div>

    <div class="trending">
      <h2>E-TRENDING</h2>
      <div class="trend" style="left:42px"><div class="trend-icon"><svg width="32" height="24" viewBox="0 0 32 24"><rect x="5" y="2" width="22" height="15" fill="none" stroke="#fff" stroke-width="2.5"/><path d="M1 21h30" stroke="#fff" stroke-width="3"/></svg></div>The Digital Revolution</div>
      <div class="trend" style="left:130px"><div class="trend-icon"><svg width="30" height="26" viewBox="0 0 30 26"><path d="M3 9h6l12-7v20L9 15H3z" fill="#fff"/><path d="M8 15l2 9h4l-2-9" fill="#fff"/><path d="M25 8v8" stroke="#fff" stroke-width="2.5"/></svg></div>Superannuation: Recent News &amp; Announcements</div>
      <div class="trend" style="left:218px"><div class="trend-icon"><svg width="24" height="30" viewBox="0 0 24 30"><rect x="2" y="2" width="20" height="26" rx="2" fill="none" stroke="#fff" stroke-width="2.5"/><rect x="6" y="6" width="12" height="5" fill="#fff"/><path d="M6 15h3M11 15h3M16 15h2M6 19h3M11 19h3M16 19h2M6 23h3M11 23h3M16 23h2" stroke="#fff" stroke-width="2.5"/></svg></div>Preparing for the 2019 Tax Year</div>
      <div class="trend" style="left:306px"><div class="trend-icon"><svg width="28" height="22" viewBox="0 0 28 22"><path d="M2 3h24M2 11h24M2 19h24" stroke="#fff" stroke-width="3.5"/></svg></div>Loyalty Pricing Packages For Existing clients COMING SOON!</div>
    </div>
    <footer class="page-footer"><div class="brand">SOLSTICE ADVISORY<small>Clear advice. Real results</small></div><div class="rule"></div><div class="url">www.solsticeadvisory.com.au</div><div class="num">02</div></footer>
  </article>
</section>

</body>
</html>
```